Harold: A Crossing

I need a front, back and spine cover for e and print for a short book. The book is called Harold, subtitle, A Crossing. It is about an eyewitness to the Archangel Harold. I would like to use the design many times with different colours for a series in spirituality and magic. So hopefully I can work with the designer again. The simple idea, is a plain cover in a colour, here blue. Mostly a font based cover, with a small symbolic image silhouetted at the bottom. Other covers will be orange, same font, and a different silhouette symbolic image and so on.

We need: a blue that will print well and look good on a screen. Serious, inviting honesty and truth and not flat. A font that is modern, female, says mystic but not old saint. The author is female and an award-winning writer in different areas. We need a uniform space for a title, (here Harold), a uniform space for "A Crossing", a small space for a simple symbolic image, and author name, Renata Vossel. The small image on this blue cover should be in red. Ideas would be a simple rose head. The cover must look modern and professional and compliment the brand at www.renatavossel-example.com.

If the designer would simultaneously like to pitch to design the whole series (which will have many titles), another one would be a warm/hot pink background with the title Lamp Hour, subtitle, Brighten Shared Evenings Gently. Small image silhouetted in orange might be a small gift shape, or a seahorse. Same author name, Renata Vossel. Another cover would be green background, title Stillwater: subtitle, Nine Doors Beyond Old Routine. Image in yellow: a rolled yoga mat, or an Om symbol. Renata Vossel. If we find a groove for the whole series, I can keep working with the same designer. Of course, the cover just for Harold is fine here, but please bear in mind it fits into this wider series. Blue covers are about conversation with or contact with key spiritual figures, each from the author's own personal experience. Another one there would be "Baba Tirunel", A Meeting beside Northern Waters. Image would be a simple daisy or a trophy emblem in red.

Font is crucial here and will define a series. Modern spirituality for the current generation. It must suggest contact with higher planes without being chintzy. Thank you!

Simple designs are iconic. That is what we are going for!

Good luck.

Target Market(s)

The people who read iconic series books like old kestrel editions

Colors
34a6d7

Requirements
Must have
• modern, iconic, translatable into different markets.
Nice to have
• symbolic images silhouetted into a colour, not black, as the guidelines.
Should not have
• not too emotional.

```html
<!DOCTYPE html>
<html lang="en">
<head>
<meta charset="utf-8">
<title>Renata Vossel — Spirituality Series Covers</title>
<link rel="stylesheet" href="https://fonts.googleapis.com/css2?family=Della+Respira&family=Oswald:wght@300&family=Lato:wght@400&display=swap">
<style>
  :root {
    --page-bg: #ffffff;
    --ink-light: #ffffff;
    --blue-top: #0046d9;
    --blue-bottom: #00abf1;
    --pink-top: #e4005e;
    --pink-bottom: #f500c2;
    --green-top: #5daf24;
    --green-bottom: #c9e566;
    --emblem-red: #e0262c;
    --emblem-violet: #8c2fe0;
    --emblem-yellow: #f2f000;
  }
  * { margin: 0; padding: 0; box-sizing: border-box; }
  html, body {
    width: 1200px;
    height: 840px;
    overflow: hidden;
    background: var(--page-bg);
  }
  .series {
    position: relative;
    width: 1200px;
    height: 840px;
  }
  .cover {
    position: absolute;
    top: 161px;
    width: 343px;
    height: 518px;
    color: var(--ink-light);
    text-align: center;
  }
  .cover--blue  { left: 46px;  background: linear-gradient(180deg, var(--blue-top), var(--blue-bottom)); }
  .cover--pink  { left: 427px; background: linear-gradient(180deg, var(--pink-top), var(--pink-bottom)); }
  .cover--green { left: 809px; background: linear-gradient(180deg, var(--green-top), var(--green-bottom)); }

  .cover__title {
    position: absolute;
    left: 0; right: 0;
    top: 118px;
    font-family: "Della Respira", serif;
    font-weight: 400;
    font-size: 56px;
    line-height: 1;
    letter-spacing: -0.5px;
  }
  .cover__subtitle {
    position: absolute;
    left: 0; right: 0;
    top: 187px;
    font-family: "Oswald", sans-serif;
    font-weight: 300;
    font-size: 19px;
    line-height: 1;
  }
  .cover__emblem {
    position: absolute;
    left: 50%;
    top: 316px;
    width: 50px;
    height: 50px;
    transform: translateX(-50%);
  }
  .cover__author {
    position: absolute;
    left: 0; right: 0;
    top: 421px;
    font-family: "Lato", sans-serif;
    font-size: 17px;
    letter-spacing: 0.8px;
    text-transform: uppercase;
  }
</style>
</head>
<body>
<main class="series">
  <article class="cover cover--blue">
    <h1 class="cover__title">Harold</h1>
    <p class="cover__subtitle">A Crossing</p>
    <svg class="cover__emblem" viewBox="0 0 50 50" role="img" aria-label="Small red rose head silhouette">
      <rect x="7" y="6" width="36" height="38" rx="14" fill="var(--emblem-red)"/>
    </svg>
    <p class="cover__author">Renata Vossel</p>
  </article>

  <article class="cover cover--pink">
    <h1 class="cover__title">Lamp Hour</h1>
    <p class="cover__subtitle">Brighten Shared Evenings Gently</p>
    <svg class="cover__emblem" viewBox="0 0 50 50" role="img" aria-label="Small violet seahorse silhouette">
      <rect x="14" y="2" width="22" height="46" rx="10" fill="var(--emblem-violet)"/>
    </svg>
    <p class="cover__author">Renata Vossel</p>
  </article>

  <article class="cover cover--green">
    <h1 class="cover__title">Stillwater</h1>
    <p class="cover__subtitle">Nine Doors Beyond Old Routine</p>
    <svg class="cover__emblem" viewBox="0 0 50 50" role="img" aria-label="Small yellow Om symbol within a lotus flower">
      <circle cx="25" cy="25" r="22" fill="var(--emblem-yellow)"/>
    </svg>
    <p class="cover__author">Renata Vossel</p>
  </article>
</main>
</body>
</html>
```